Vibrant, yet professional, stationery set and other designs required.

I need to source a fantastic designer for a new project as part of my company using a new logo designed via sketch harbor.

**UPDATE** I am not looking for just 'fine' design that will suffice. I am looking for something great.

We are a life assurance brokerage based in Dublin, Ireland and BrightRoost.ie is our new website aimed at providing services for young families in Ireland. We are hoping to be the 'Velro' level of service providers in this area and I am looking for the quality of design to reflect this :-) Hopefully that makes sense!

I have a preference for straight lines over curves and waves.

I need...

1. Business card
2. Letterhead
3. Banner (for printing - 76cm X 305cm)
4. Car branding for KORVA 9 (2014 sport model) I believe the templates are freely available online.

Target Market(s)

Parents in Ireland - Aged 27 to 50.

Industry/Entity Type

Financial Planning

Colors

Designer to choose colors to be used in the design.

Requirements
Must have
• All of the items listed in the description above. I like clean, bright, legible, vibrant and professional design.
Should not have
• No silly or 'cheap' looking designs. This is a professional company looking to provide a professional service.

```html
<!DOCTYPE html>
<html lang="en">
<head>
<meta charset="utf-8">
<title>BrightRoost.ie — Business Card</title>
<link rel="stylesheet" href="https://fonts.googleapis.com/css2?family=Roboto:wght@400;500;700&display=swap">
<style>
  :root {
    --backdrop: #cfcfcf;
    --brand-orange: #f0821a;
    --card-white: #f6f6f6;
    --logo-grey: #8c979b;
    --text-grey: #4f5455;
    --title-grey: #8a9497;
    --band-grey: #8f9a9c;
    --band-text: #ffffff;
  }
  * { margin: 0; padding: 0; box-sizing: border-box; }
  html, body {
    width: 1200px;
    height: 960px;
    overflow: hidden;
    background: var(--backdrop);
    font-family: "Roboto", Arial, sans-serif;
  }
  .canvas { position: relative; width: 1200px; height: 960px; }

  .card {
    position: absolute;
    left: 320px;
    width: 600px;
    height: 345px;
  }

  /* Front */
  .card-front {
    top: 105px;
    background: var(--brand-orange);
    display: flex;
    align-items: center;
    justify-content: center;
    padding-top: 14px;
  }
  .front-wordmark {
    color: #ffffff;
    font-weight: 700;
    font-size: 54px;
    letter-spacing: -1px;
  }

  /* Back */
  .card-back {
    top: 493px;
    background: var(--card-white);
  }
  .back-wordmark {
    position: absolute;
    left: 29px;
    top: 68px;
    color: var(--logo-grey);
    font-weight: 700;
    font-size: 44px;
    line-height: 52px;
    letter-spacing: -1px;
  }
  .address {
    position: absolute;
    left: 29px;
    top: 175px;
    color: var(--text-grey);
    font-size: 14px;
    line-height: 18px;
  }
  .contact-list {
    position: absolute;
    left: 29px;
    top: 219px;
    list-style: none;
    color: var(--text-grey);
    font-size: 14px;
  }
  .contact-item {
    display: flex;
    align-items: center;
    height: 19.5px;
  }
  .contact-icon {
    width: 14px;
    height: 14px;
    margin-right: 9px;
    fill: var(--brand-orange);
  }
  .person {
    position: absolute;
    right: 28px;
    top: 214px;
    text-align: right;
  }
  .person-name {
    color: var(--brand-orange);
    font-weight: 500;
    font-size: 19px;
    line-height: 22px;
  }
  .person-title {
    color: var(--title-grey);
    font-weight: 500;
    font-size: 14px;
    line-height: 22px;
  }
  .web-band {
    position: absolute;
    left: 0;
    bottom: 0;
    width: 100%;
    height: 29px;
    background: var(--band-grey);
    color: var(--band-text);
    font-weight: 700;
    font-size: 13px;
    letter-spacing: 7px;
    line-height: 29px;
    padding-left: 30px;
  }
</style>
</head>
<body>
<main class="canvas">
  <section class="card card-front" aria-label="Business card front">
    <span class="front-wordmark">BrightRoost.ie</span>
  </section>

  <section class="card card-back" aria-label="Business card back">
    <span class="back-wordmark">BrightRoost.ie</span>

    <p class="address">12 Larkfield Row<br>Dublin 6W, Ireland</p>

    <ul class="contact-list">
      <li class="contact-item">
        <svg class="contact-icon" viewBox="0 0 16 16" aria-hidden="true"><path d="M3.5 1l2.6 3-1.5 2a8 8 0 0 0 5 5l2-1.5 3 2.6-1.6 2.4C7 14.5 1.5 9 1 2.6z"/></svg>
        01 490 7735
      </li>
      <li class="contact-item">
        <svg class="contact-icon" viewBox="0 0 16 16" aria-hidden="true"><path d="M4 0h8v16H4zM5.5 2v10h5V2zM7 13.2h2v1.4H7z" fill-rule="evenodd"/></svg>
        087 515 3046
      </li>
      <li class="contact-item">
        <svg class="contact-icon" viewBox="0 0 16 16" aria-hidden="true"><path d="M4 1h8v4H4zM1 6h14v6h-2v3H3v-3H1zM4.5 10v3.5h7V10z" fill-rule="evenodd"/></svg>
        01 476 2280
      </li>
      <li class="contact-item">
        <svg class="contact-icon" viewBox="0 0 16 16" aria-hidden="true"><path d="M1 3h14v1.5L8 9 1 4.5zM1 6.3l7 4.5 7-4.5V13H1z"/></svg>
        hello@brightroost.ie
      </li>
    </ul>

    <div class="person">
      <p class="person-name">CIARA DOYLE</p>
      <p class="person-title">CEO/FOUNDER</p>
    </div>

    <div class="web-band">www.brightroost.ie</div>
  </section>
</main>
</body>
</html>
```